Quorva - corporate Business Card

We need a good look and innovative business card for a new start up company based in Los Angeles called "Quorva". We are in a payment business, including payment card, app, and ewallet. We are expert in online payment and Card not present (CNP) transaction.
We need an innovative, modern business card.

Our logo font is Aero Matics

Target Market(s)

Startup - Bank - Online Payment - Card Manufacturing

Industry/Entity Type

Startup

Contact Information for Business Card

phone: 555 014 7396 - Address: 4172 Marlowe blvd, Harlow Heights, NV 89011

Requirements
Must have
• Message: innovative, professional, expert, high tech, trust, online payment expert, security
Nice to have
• no comment
Should not have
• no Comment

```html
<!DOCTYPE html>
<html lang="en">
<head>
<meta charset="utf-8">
<title>Quorva – Business Card</title>
<link href="https://fonts.googleapis.com/css2?family=Open+Sans:wght@400;600;700&display=swap" rel="stylesheet">
<style>
  :root {
    --brand-red: #b81f2e;
    --brand-red-deep: #ab1c2a;
    --card-white: #ffffff;
    --tint-blush: #f6ece9;
    --ink-grey: #707070;
    --rule-grey: #8a8a8a;
    --backdrop: #3b3532;
  }
  * { margin: 0; padding: 0; box-sizing: border-box; }
  html, body { width: 1200px; height: 780px; overflow: hidden; }
  body {
    background: var(--backdrop);
    font-family: "Open Sans", Arial, sans-serif;
    position: relative;
  }
  .card {
    position: absolute;
    top: 240px;
    width: 520px;
    height: 300px;
    overflow: hidden;
    box-shadow: 0 10px 26px rgba(0,0,0,.45);
  }
  .card--front { left: 50px; background: var(--brand-red); }
  .card--back { left: 630px; background: var(--card-white); }

  .accent-circle { position: absolute; border-radius: 50%; }
  .card--front .accent-circle {
    width: 260px; height: 260px; left: -20px; top: -50px;
    background: var(--brand-red-deep);
  }
  .card--back .accent-circle {
    width: 290px; height: 290px; left: -10px; top: -70px;
    background: var(--tint-blush);
  }

  .wordmark {
    font-weight: 700;
    letter-spacing: 1px;
    line-height: 1;
  }
  .card--front .wordmark {
    position: absolute;
    color: var(--card-white);
    font-size: 62px;
    left: 185px; top: 92px;
  }
  .brand {
    position: absolute;
    right: 36px; top: 46px;
    display: flex; align-items: center; gap: 12px;
  }
  .brand__dot {
    width: 60px; height: 60px; border-radius: 50%;
    background: var(--brand-red);
  }
  .card--back .wordmark { color: var(--brand-red); font-size: 50px; }

  .contact { position: absolute; left: 30px; top: 146px; }
  .contact__name {
    color: var(--brand-red);
    font-weight: 700;
    font-size: 17px;
    line-height: 1.15;
  }
  .contact__title {
    color: var(--ink-grey);
    font-size: 14px;
    line-height: 1.25;
  }
  .contact__list { list-style: none; margin-top: 14px; }
  .contact__item {
    display: flex; align-items: center; gap: 6px;
    color: var(--ink-grey);
    font-size: 13px;
    line-height: 1.6;
  }
  .contact__icon { width: 14px; height: 14px; flex: none; }

  .divider {
    position: absolute;
    left: 30px; right: 40px; top: 192px;
    border-top: 1px solid var(--rule-grey);
  }

  .address {
    position: absolute;
    right: 40px; bottom: 24px;
    width: 210px;
    color: var(--ink-grey);
    font-size: 13.5px;
    line-height: 1.35;
    font-style: normal;
  }
</style>
</head>
<body>
  <section class="card card--front" aria-label="Card front">
    <div class="accent-circle"></div>
    <div class="wordmark">quorva</div>
  </section>

  <section class="card card--back" aria-label="Card back">
    <div class="accent-circle"></div>
    <div class="brand">
      <span class="brand__dot"></span>
      <span class="wordmark">quorva</span>
    </div>

    <div class="contact">
      <p class="contact__name">Dana Whitlow</p>
      <p class="contact__title">Managing Director</p>
      <ul class="contact__list">
        <li class="contact__item">
          <svg class="contact__icon" viewBox="0 0 14 14" aria-hidden="true">
            <rect width="14" height="14" fill="#b81f2e"/>
            <path d="M3.5 3h2l.8 2-1.2.9a6 6 0 0 0 3 3l.9-1.2 2 .8v2a1 1 0 0 1-1 1A7.5 7.5 0 0 1 2.5 4a1 1 0 0 1 1-1z" fill="#fff"/>
          </svg>
          555 014 7396
        </li>
        <li class="contact__item">
          <svg class="contact__icon" viewBox="0 0 14 14" aria-hidden="true">
            <rect width="14" height="14" fill="#b81f2e"/>
            <rect x="2.5" y="4" width="9" height="6.5" fill="none" stroke="#fff" stroke-width="1"/>
            <path d="M2.5 4l4.5 3.6L11.5 4" fill="none" stroke="#fff" stroke-width="1"/>
          </svg>
          hello@quorvamail.com
        </li>
      </ul>
    </div>

    <div class="divider"></div>

    <address class="address">
      4172 Marlowe blvd,<br>Harlow Heights, NV 89011
    </address>
  </section>
</body>
</html>
```